Fenwick Grading LTD - website for irrigation & Landscape Lighting & Buried service wire

Looking for a website to help promote my business with Irrigation (installation, service, etc) and buried service wire/drainage solutions.

Commercial/Residential

Landscape lighting.

I’ll get photos in the trucks and trailers to upload as well maybe the machine as well.

Target Market(s)

Homeowners who want green grass and beautiful gardens. Beautiful landscape lighting

Industry/Entity Type

Irrigation systems and landscape lighting and buried service wire to homes and offering Drainage soltions.

Coding

Coded - Design and coding required

Number of Pages Required

4 page

Colors
F0912C
F2A743
F7CA91
FBE8D2
FDF5EE

Requirements
Must have
• was hoping to link up my email on fenwickgrading@mailbox-example.net with the website if possible.
Nice to have
• Page for Irrigation, page for landscape lighting, page buried service wire & drainage soltions.

```html
<!DOCTYPE html>
<html lang="en">
<head>
<meta charset="utf-8">
<title>Irrigation – Fenwick Grading LTD</title>
<link href="https://fonts.googleapis.com/css2?family=Roboto+Condensed:wght@500;700&family=Montserrat:wght@400;500;600&display=swap" rel="stylesheet">
<style>
:root{
  --orange:#F0912C;
  --orange-2:#F2A743;
  --orange-3:#F7CA91;
  --orange-4:#FBE8D2;
  --orange-5:#FDF5EE;
  --ink:#111111;
  --text:#4a4a4a;
  --muted:#9a9a9a;
  --white:#ffffff;
  --black:#000000;
}
*{margin:0;padding:0;box-sizing:border-box}
html,body{width:1200px;height:4323px;overflow:hidden;background:var(--white)}
body{position:relative;font-family:"Montserrat",sans-serif;color:var(--text)}
.abs{position:absolute}
.heading{font-family:"Roboto Condensed",sans-serif;font-weight:700;color:var(--ink);text-align:center;width:1200px;left:0}
.heading span{color:var(--orange)}

/* hero */
.hero-bg{left:0;top:0}
.brand{font-family:"Montserrat",sans-serif;font-weight:600;color:var(--orange);text-transform:uppercase;letter-spacing:2px;line-height:1.15;display:flex;align-items:center;gap:10px}
.brand-mark{width:14px;height:14px;background:var(--orange);flex:none}
.hero-brand{left:141px;top:28px;font-size:17px}
.nav a{position:absolute;top:33px;font-size:13.5px;color:var(--white);text-decoration:none;font-weight:400}
.nav a.active{color:var(--orange);border-bottom:1px solid var(--orange);padding-bottom:1px}
.btn{background:var(--orange);color:var(--white);font-weight:600;text-transform:uppercase;text-align:center;border-radius:30px;letter-spacing:.5px}
.nav-btn{left:940px;top:23px;width:117px;height:37px;line-height:37px;font-size:11.5px}
.page-title{left:141px;top:186px;font-family:"Roboto Condensed",sans-serif;font-weight:700;color:var(--white);font-size:35px}
.crumb{left:141px;top:231px;font-size:12.5px;color:var(--white)}
.crumb b{font-weight:600}

/* intro */
.intro-title{top:518px;font-size:40px}
.intro-sub{top:580px;width:1200px;text-align:center;font-size:13px;font-weight:500;color:var(--ink)}
.intro-text{left:148px;top:614px;width:904px;text-align:center;font-size:13px;line-height:22.6px}
.services-title{top:772px;font-size:40px}

/* services */
.service-head{font-size:13px;font-weight:500;color:var(--ink);border-left:2px solid var(--orange);padding:9px 0 9px 10px}
.service-text{font-size:13px;line-height:22.6px;width:420px}
.tri{position:absolute}

/* why */
.why-title{top:2370px;font-size:40px}
.card{position:absolute;top:2463px;width:219px;height:361px;border-radius:14px;border:1px solid var(--orange-4);background:var(--white);box-shadow:0 4px 14px rgba(240,145,44,.08);text-align:center;padding:0 10px}
.card.featured{background:var(--orange);border-color:var(--orange)}
.card svg{margin-top:32px}
.card h3{font-size:13px;font-weight:500;color:var(--ink);margin-top:12px;line-height:22px}
.card p{font-size:9.8px;line-height:17.6px;color:var(--text);margin-top:4px}
.card.featured h3{color:var(--white)}
.card.featured p{color:var(--orange-4)}

/* contact band */
.cta-title{top:2982px;font-size:37px;color:var(--white)}
.cta-text{left:180px;top:3050px;width:840px;text-align:center;font-size:12.8px;line-height:22px;color:var(--white)}
.cta-btn{left:549px;top:3146px;width:102px;height:34px;line-height:34px;font-size:11.5px}

/* quote */
.quote-title{top:3340px;font-size:37px}
.field{position:absolute;border:1px solid #e3e3e3;border-radius:4px;font-size:12px;color:#b5b5b5;padding:0 26px;line-height:49px}
.submit{left:545px;top:3772px;width:109px;height:37px;line-height:37px;font-size:11.5px}

/* footer */
.footer-bg{left:0;top:3890px}
.footer-brand{left:0;width:1200px;top:4000px;justify-content:center;font-size:26px}
.fnav a{position:absolute;top:4134px;font-size:12.5px;color:var(--white);text-decoration:none}
.fnav a.active{color:var(--orange)}
.fnav a.bold{font-weight:600}
.contact-item{position:absolute;top:4199px;display:flex;gap:12px;align-items:center;color:var(--white);font-size:12.5px;line-height:20px;white-space:nowrap}
.contact-item .ico{width:36px;height:36px;border:1.5px solid var(--white);border-radius:50%;display:flex;align-items:center;justify-content:center;flex:none}
.rule{left:141px;top:4257px;width:918px;height:1px;background:#333}
.copy{left:141px;top:4279px;font-size:12.5px;color:var(--white)}
.social{position:absolute;top:4270px;width:33px;height:33px;border:1.5px solid var(--white);border-radius:50%;display:flex;align-items:center;justify-content:center}
</style>
</head>
<body>

<!-- HERO -->
<svg class="abs hero-bg" width="1200" height="440" viewBox="0 0 1200 440">
  <defs>
    <linearGradient id="heroGrad" x1="0" y1="0" x2="1" y2="1">
      <stop offset="0" stop-color="#2f3a22"/>
      <stop offset=".45" stop-color="#55702f"/>
      <stop offset="1" stop-color="#3a3a2a"/>
    </linearGradient>
  </defs>
  <polygon points="0,0 1200,0 1200,364 600,426 0,364" fill="url(#heroGrad)" role="img" aria-label="Photo of a landscaped garden with curved stone border, green lawn and a garden light"/>
  <polygon points="0,0 1200,0 1200,364 600,426 0,364" fill="rgba(0,0,0,.28)"/>
  <polyline points="0,368 600,432 1200,368" fill="none" stroke="#F0912C" stroke-width="3"/>
</svg>

<div class="abs brand hero-brand"><span class="brand-mark"></span><span>Fenwick<br>Grading LTD</span></div>
<nav class="nav">
  <a style="left:408px">Home</a>
  <a class="active" style="left:493px">Irrigation</a>
  <a style="left:597px">Landscape Lighting</a>
  <a style="left:770px">Trenching&nbsp; Services</a>
</nav>
<div class="abs btn nav-btn">Contact Us</div>
<h1 class="abs page-title">Irrigation</h1>
<div class="abs crumb">Home » <b>Irrigation</b></div>

<!-- INTRO -->
<h2 class="abs heading intro-title">Irrigation <span>Systems</span></h2>
<p class="abs intro-sub">Expert Irrigation Installations and Service Calls</p>
<p class="abs intro-text">Welcome to FenwickGrading Irrigation Systems, your trusted provider of professional irrigation installations and reliable service calls. We specialize in delivering top-quality irrigation solutions for residential, commercial, and agricultural properties. Whether you need a new system installation or assistance with troubleshooting and maintenance, we have the expertise and experience to meet all your irrigation needs.</p>

<h2 class="abs heading services-title">Our <span>Services</span></h2>

<!-- SERVICES -->
<svg class="tri" style="left:176px;top:888px" width="334" height="300" viewBox="0 0 334 300">
  <defs><linearGradient id="g1" x1="0" y1="0" x2="0" y2="1"><stop offset="0" stop-color="#7fa65a"/><stop offset="1" stop-color="#3f5e2c"/></linearGradient></defs>
  <polyline points="16,3 166,294 328,3" fill="none" stroke="#F0912C" stroke-width="1.5"/>
  <polygon points="4,3 164,284 326,3" fill="url(#g1)" role="img" aria-label="Photo of a sprinkler head spraying water over a lawn"/>
</svg>
<div class="abs service-head" style="left:616px;top:946px">Irrigation Installations</div>
<p class="abs service-text" style="left:616px;top:999px">We offer comprehensive irrigation system installations tailored to meet your specific requirements. Our team of skilled technicians will assess your property, design a customized irrigation system, and handle the entire installation process. We work with the latest technology and high-quality equipment to ensure efficient water distribution and optimal plant health.</p>

<div class="abs service-head" style="left:180px;top:1324px">System Upgrades and Additions</div>
<p class="abs service-text" style="left:180px;top:1378px">If you currently have an irrigation system that needs upgrading or expanding, we can help. Our experienced professionals will assess your existing system, identify areas for improvement, and provide cost-effective solutions to enhance its performance. We can add additional zones, upgrade controllers, or integrate smart irrigation technologies for improved water management.</p>
<svg class="tri" style="left:694px;top:1268px" width="334" height="300" viewBox="0 0 334 300">
  <defs><linearGradient id="g2" x1="0" y1="0" x2="1" y2="1"><stop offset="0" stop-color="#5b4a32"/><stop offset=".5" stop-color="#7d8a4a"/><stop offset="1" stop-color="#c9a68a"/></linearGradient></defs>
  <polyline points="16,3 166,294 328,3" fill="none" stroke="#F0912C" stroke-width="1.5"/>
  <polygon points="4,3 164,284 326,3" fill="url(#g2)" role="img" aria-label="Photo of hands pruning a plant with garden shears"/>
</svg>

<svg class="tri" style="left:176px;top:1649px" width="334" height="300" viewBox="0 0 334 300">
  <defs><linearGradient id="g3" x1="0" y1="0" x2="1" y2="1"><stop offset="0" stop-color="#9db56a"/><stop offset=".5" stop-color="#7a6450"/><stop offset="1" stop-color="#3d4a2a"/></linearGradient></defs>
  <polyline points="16,3 166,294 328,3" fill="none" stroke="#F0912C" stroke-width="1.5"/>
  <polygon points="4,3 164,284 326,3" fill="url(#g3)" role="img" aria-label="Photo of a gardener tending plants in a greenhouse"/>
</svg>
<div class="abs service-head" style="left:616px;top:1693px">Repairs and Maintenance</div>
<p class="abs service-text" style="left:616px;top:1747px">We understand that irrigation systems require regular maintenance and occasional repairs to operate at their best. Our skilled technicians are available to address any issues that may arise, such as broken sprinkler heads, leaking pipes, malfunctioning valves, or controller problems. With our prompt and reliable service, we will have your system back up and running efficiently in no time.</p>

<div class="abs service-head" style="left:180px;top:2033px">Seasonal Adjustments and Programming</div>
<p class="abs service-text" style="left:180px;top:2087px">Properly adjusting and programming your irrigation system for each season is crucial to ensure water efficiency and avoid over or under watering. Our experts will fine-tune your system's settings, schedule, and watering duration based on weather conditions and the specific needs of your landscape. This will help you conserve water, save money on utility bills, and maintain a healthy and vibrant landscape throughout the year.</p>
<svg class="tri" style="left:694px;top:1986px" width="334" height="300" viewBox="0 0 334 300">
  <defs><linearGradient id="g4" x1="0" y1="0" x2="1" y2="1"><stop offset="0" stop-color="#c46a8a"/><stop offset=".5" stop-color="#8aa060"/><stop offset="1" stop-color="#dcdcd6"/></linearGradient></defs>
  <polyline points="16,3 166,294 328,3" fill="none" stroke="#F0912C" stroke-width="1.5"/>
  <polygon points="4,3 164,284 326,3" fill="url(#g4)" role="img" aria-label="Photo of a gardener watering hanging flower baskets in a greenhouse"/>
</svg>

<!-- WHY CHOOSE US -->
<h2 class="abs heading why-title">Why <span>Choose Us</span></h2>

<div class="card" style="left:143px">
  <svg width="86" height="86" viewBox="0 0 86 86"><circle cx="43" cy="43" r="42" fill="none" stroke="#F0912C" stroke-width="1"/><path d="M30 55h26M43 25l4 9 9 1-7 6 2 9-8-5-8 5 2-9-7-6 9-1z" fill="none" stroke="#F0912C" stroke-width="1.5" stroke-linejoin="round"/></svg>
  <h3>Expertise and Experience</h3>
  <p>With years of experience in the industry, we have gained extensive knowledge and expertise in irrigation installations and services. Our team stays updated with the latest industry trends and best practices to provide you with the most reliable and efficient solutions.</p>
</div>
<div class="card" style="left:376px">
  <svg width="86" height="86" viewBox="0 0 86 86"><circle cx="43" cy="43" r="42" fill="none" stroke="#F0912C" stroke-width="1"/><path d="M31 46h24l-3 14H34z" fill="none" stroke="#F0912C" stroke-width="1.5" stroke-linejoin="round"/><path d="M43 46V28M43 46l-8-12M43 46l8-12" fill="none" stroke="#F0912C" stroke-width="1.5" stroke-linecap="round"/></svg>
  <h3>Quality Products and<br>Materials</h3>
  <p>We only work with reputable manufacturers and top-quality materials to ensure the longevity and reliability of your irrigation system. Our commitment to using premium products guarantees that you receive excellent value for your investment.</p>
</div>
<div class="card featured" style="left:607px">
  <svg width="86" height="86" viewBox="0 0 86 86"><circle cx="43" cy="43" r="42" fill="none" stroke="#ffffff" stroke-width="1"/><circle cx="35" cy="36" r="7" fill="none" stroke="#fff" stroke-width="1.5"/><circle cx="51" cy="36" r="7" fill="none" stroke="#fff" stroke-width="1.5"/><path d="M33 58h20M43 46v12" fill="none" stroke="#fff" stroke-width="1.5" stroke-linecap="round"/></svg>
  <h3>personalized approach</h3>
  <p>We understand that every property has unique irrigation needs. That's why we take a personalized approach to our services. Our team will work closely with you to understand your specific requirements, preferences, and budget, and provide tailored solutions that suit your landscape perfectly.</p>
</div>
<div class="card" style="left:839px">
  <svg width="86" height="86" viewBox="0 0 86 86"><circle cx="43" cy="43" r="42" fill="none" stroke="#F0912C" stroke-width="1"/><circle cx="46" cy="36" r="9" fill="none" stroke="#F0912C" stroke-width="1.5"/><path d="M26 52l8-4h10l8 4 8-6" fill="none" stroke="#F0912C" stroke-width="1.5" stroke-linecap="round" stroke-linejoin="round"/></svg>
  <h3>Outstanding Customer<br>Service</h3>
  <p>At FenwickGrading Irrigation Systems, customer satisfaction is our top priority. We strive to deliver exceptional customer service, from the initial consultation to the completion of the project and beyond. Our friendly and professional team is always ready to address your concerns, answer your questions, and provide ongoing support.</p>
</div>

<!-- CONTACT BAND -->
<svg class="abs" style="left:0;top:2908px" width="1200" height="354" viewBox="0 0 1200 354">
  <defs><linearGradient id="band" x1="0" y1="0" x2="0" y2="1"><stop offset="0" stop-color="#3e4a3a"/><stop offset=".5" stop-color="#2c3a22"/><stop offset="1" stop-color="#1f2a18"/></linearGradient></defs>
  <rect width="1200" height="354" fill="url(#band)" role="img" aria-label="Photo of sprinklers watering rows of crops in a field at dusk"/>
  <rect width="1200" height="354" fill="rgba(0,0,0,.35)"/>
</svg>
<h2 class="abs heading cta-title">Contact <span>FenwickGrading</span> Irrigation Systems Today</h2>
<p class="abs cta-text">For professional irrigation installations, reliable service calls, and expert advice, choose FenwickGrading Irrigation Systems With our comprehensive range of services, unmatched expertise, and commitment to customer satisfaction, we are your go-to irrigation solution provider. Contact us today to discuss your needs and schedule an appointment.</p>
<div class="abs btn cta-btn">Contact</div>

<!-- QUOTE FORM -->
<h2 class="abs heading quote-title">Get A <span>Free Quote</span></h2>
<div class="field" style="left:275px;top:3418px;width:317px;height:49px">First Name*</div>
<div class="field" style="left:607px;top:3418px;width:317px;height:49px">Last Name*</div>
<div class="field" style="left:275px;top:3490px;width:317px;height:49px">Email Address*</div>
<div class="field" style="left:607px;top:3490px;width:317px;height:49px">Phone Number*</div>
<div class="field" style="left:275px;top:3562px;width:649px;height:49px">Irrigation</div>
<div class="field" style="left:275px;top:3634px;width:649px;height:95px;line-height:44px">Message*</div>
<div class="abs btn submit">Submit</div>

<!-- FOOTER -->
<svg class="abs footer-bg" width="1200" height="433" viewBox="0 0 1200 433">
  <polygon points="0,84 600,8 1200,84 1200,433 0,433" fill="#000000"/>
  <polyline points="0,82 600,5 1200,82" fill="none" stroke="#F0912C" stroke-width="3"/>
</svg>
<div class="abs brand footer-brand"><span class="brand-mark"></span><span>Fenwick<br>Grading LTD</span></div>
<nav class="fnav">
  <a style="left:279px">Home</a>
  <a class="active" style="left:373px">Irrigation</a>
  <a style="left:489px">Landscape Lighting</a>
  <a style="left:672px">Trenching&nbsp; Services</a>
  <a class="bold" style="left:852px">Contact Us</a>
</nav>
<div class="contact-item" style="left:205px">
  <span class="ico"><svg width="14" height="16" viewBox="0 0 14 16"><path d="M7 15s5-5 5-9A5 5 0 0 0 2 6c0 4 5 9 5 9z" fill="#fff"/><circle cx="7" cy="6" r="2" fill="#000"/></svg></span>
  <span>210 Millbrook Road<br>Hollis Bay, ON K0L 2X0</span>
</div>
<div class="contact-item" style="left:527px">
  <span class="ico"><svg width="15" height="15" viewBox="0 0 24 24"><path d="M6.6 10.8a15 15 0 0 0 6.6 6.6l2.2-2.2c.3-.3.7-.4 1-.2 1.1.4 2.3.6 3.6.6.6 0 1 .4 1 1V20c0 .6-.4 1-1 1A17 17 0 0 1 3 4c0-.6.4-1 1-1h3.5c.6 0 1 .4 1 1 0 1.3.2 2.5.6 3.6.1.3 0 .7-.2 1z" fill="#fff"/></svg></span>
  <span>Phone<br>555-014-2376</span>
</div>
<div class="contact-item" style="left:764px">
  <span class="ico"><svg width="15" height="12" viewBox="0 0 15 12"><rect width="15" height="12" rx="1.5" fill="#fff"/><path d="M1 1.5l6.5 5 6.5-5" fill="none" stroke="#000" stroke-width="1.3"/></svg></span>
  <span>E-Mail<br>info@fenwickgrading-example.net</span>
</div>
<div class="abs rule"></div>
<p class="abs copy">© 2024 Fenwick Grading LTD . All Rights Reserved.</p>
<span class="social" style="left:904px" aria-label="Social profile link"><svg width="12" height="12" viewBox="0 0 12 12"><path d="M3 9L9 3M4 3h5v5" fill="none" stroke="#fff" stroke-width="1.4" stroke-linecap="round" stroke-linejoin="round"/></svg></span>
<span class="social" style="left:945px" aria-label="Social profile link"><svg width="12" height="12" viewBox="0 0 12 12"><path d="M3 9L9 3M4 3h5v5" fill="none" stroke="#fff" stroke-width="1.4" stroke-linecap="round" stroke-linejoin="round"/></svg></span>
<span class="social" style="left:985px" aria-label="Social profile link"><svg width="12" height="12" viewBox="0 0 12 12"><path d="M3 9L9 3M4 3h5v5" fill="none" stroke="#fff" stroke-width="1.4" stroke-linecap="round" stroke-linejoin="round"/></svg></span>
<span class="social" style="left:1025px" aria-label="Social profile link"><svg width="12" height="12" viewBox="0 0 12 12"><path d="M3 9L9 3M4 3h5v5" fill="none" stroke="#fff" stroke-width="1.4" stroke-linecap="round" stroke-linejoin="round"/></svg></span>

</body>
</html>
```